Bridgeway Health of Nations

Please design a business card that is colorful but at the same time easy to read. We are based out on Miami Florida. We are a small start up healthcare company that has been in operation for 1 year. Our clients are Hospitals, Insurance companies, and Manage Care health companies. We are growing quickly and lead the niche we are in. Please make the card 2 sided on the front will be the typical info. Logo, Company Name, Persons Name, Title, Cell #, Office #, Fax#, email, website. No address. On the back we will list 5 services that we do. For example Care Transitions, Case management, Risk assessment, Utilization Review.
Target Market(s)
CEO's and COO's of hospitals and healthcare companies.
Industry/Entity Type
Healthcare

```html
<!DOCTYPE html>
<html lang="en">
<head>
<meta charset="utf-8">
<title>Bridgeway Health of Nations – Business Card</title>
<link href="https://fonts.googleapis.com/css2?family=Arimo:wght@400;700&family=Open+Sans:wght@400;600;700&display=swap" rel="stylesheet">
<style>
  :root {
    --bg: #e6e7e9;
    --card-white: #f7f7f8;
    --brand-blue: #1f6fd0;
    --brand-blue-dark: #1552a8;
    --brand-blue-light: #3a8be6;
    --ink: #3a3a40;
    --on-blue: #ffffff;
    --rule-on-blue: rgba(255,255,255,0.45);
    --rule-light: #cfd6e2;
  }
  * { box-sizing: border-box; margin: 0; padding: 0; }
  html, body { width: 1200px; height: 990px; overflow: hidden; }
  body {
    background: var(--bg);
    position: relative;
    font-family: "Open Sans", Arial, sans-serif;
  }
  .card {
    position: absolute;
    top: 128px;
    width: 420px;
    height: 734px;
    background: var(--card-white);
    box-shadow: 0 10px 28px rgba(0,0,0,0.18);
    overflow: hidden;
  }
  .card--front { left: 150px; }
  .card--back { left: 630px; border: 24px solid var(--brand-blue); }

  .brand {
    position: absolute;
    display: flex;
    align-items: center;
    gap: 18px;
  }
  .brand__dot {
    width: 46px; height: 46px;
    border-radius: 50%;
    background: var(--brand-blue);
    flex: none;
  }
  .brand__name {
    font-family: "Arimo", Arial, sans-serif;
    font-weight: 700;
    color: var(--ink);
    font-size: 30px;
    line-height: 1.08;
  }
  .card--front .brand { left: 72px; top: 96px; }
  .card--back .brand { left: 60px; top: 100px; }
  .card--back .brand__name { font-size: 38px; }
  .card--back .brand__dot { width: 56px; height: 56px; }

  .contact-panel {
    position: absolute;
    left: 0; right: 26px; bottom: 0;
    height: 450px;
    background: linear-gradient(160deg, var(--brand-blue-light) 0%, var(--brand-blue) 45%, var(--brand-blue-dark) 100%);
    color: var(--on-blue);
    text-align: center;
    padding-top: 34px;
  }
  .contact-panel__name {
    font-size: 30px;
    font-weight: 600;
    letter-spacing: 0.5px;
    line-height: 1.3;
  }
  .contact-panel__title {
    font-size: 14px;
    letter-spacing: 2px;
    margin-top: 2px;
    opacity: 0.9;
  }
  .contact-list { list-style: none; margin: 22px auto 0; width: 290px; }
  .contact-list__item {
    padding: 8px 0 9px;
    border-top: 1px solid var(--rule-on-blue);
    font-size: 15px;
    line-height: 1.35;
  }
  .contact-list__item:first-child { border-top: 0; }
  .contact-list__icon { display: block; margin: 0 auto 3px; width: 15px; height: 15px; }
  .contact-list__label { font-weight: 600; margin-right: 6px; }

  .services {
    position: absolute;
    left: 60px; right: 40px; top: 380px;
    list-style: none;
    border-top: 2px solid var(--brand-blue);
    padding-top: 18px;
  }
  .services__item {
    display: flex;
    align-items: center;
    gap: 12px;
    font-size: 19px;
    font-weight: 600;
    color: var(--ink);
    padding: 10px 0;
    border-bottom: 1px solid var(--rule-light);
  }
  .services__item:last-child { border-bottom: 0; }
  .services__tick { width: 18px; height: 18px; flex: none; }
</style>
</head>
<body>
  <section class="card card--front" aria-label="Business card front">
    <div class="brand">
      <span class="brand__dot"></span>
      <p class="brand__name">Bridgeway<br>Health of<br>Nations</p>
    </div>
    <div class="contact-panel">
      <h1 class="contact-panel__name">DANIEL REYES</h1>
      <p class="contact-panel__title">GENERAL MANAGER</p>
      <ul class="contact-list">
        <li class="contact-list__item">
          <svg class="contact-list__icon" viewBox="0 0 24 24" fill="#fff"><path d="M7 2h10a1 1 0 0 1 1 1v18a1 1 0 0 1-1 1H7a1 1 0 0 1-1-1V3a1 1 0 0 1 1-1zm1 3v13h8V5zm4 14.2a1 1 0 1 0 0 .1z"/></svg>
          <span class="contact-list__label">Cell</span>305 555 0142
        </li>
        <li class="contact-list__item">
          <svg class="contact-list__icon" viewBox="0 0 24 24" fill="#fff"><path d="M6.6 10.8a15.1 15.1 0 0 0 6.6 6.6l2.2-2.2c.3-.3.7-.4 1-.2 1.1.4 2.3.6 3.6.6.6 0 1 .4 1 1V20c0 .6-.4 1-1 1A17 17 0 0 1 3 4c0-.6.4-1 1-1h3.5c.6 0 1 .4 1 1 0 1.3.2 2.5.6 3.6.1.3 0 .7-.2 1z"/></svg>
          <span class="contact-list__label">Office</span>305 555 0100
        </li>
        <li class="contact-list__item">
          <svg class="contact-list__icon" viewBox="0 0 24 24" fill="#fff"><path d="M6 2h9l3 3v4H6zM3 10h18v9H3zm3 2v2h6v-2zm0 3v2h6v-2zm9-3v2h3v-2z"/></svg>
          <span class="contact-list__label">Fax</span>305 555 0199
        </li>
        <li class="contact-list__item">
          <svg class="contact-list__icon" viewBox="0 0 24 24" fill="#fff"><path d="M3 5h18v14H3z M4.5 6.5v.3L12 12l7.5-5.2v-.3z" fill-rule="evenodd"/></svg>
          dreyes@bridgewayhn.com
        </li>
        <li class="contact-list__item">
          <svg class="contact-list__icon" viewBox="0 0 24 24" fill="none" stroke="#fff" stroke-width="2"><circle cx="12" cy="12" r="9"/><path d="M3 12h18M12 3c3 3.5 3 14.5 0 18M12 3c-3 3.5-3 14.5 0 18"/></svg>
          www.bridgewayhn.com
        </li>
      </ul>
    </div>
  </section>

  <section class="card card--back" aria-label="Business card back">
    <div class="brand">
      <span class="brand__dot"></span>
      <p class="brand__name">Bridgeway<br>Health of<br>Nations</p>
    </div>
    <ul class="services">
      <li class="services__item"><svg class="services__tick" viewBox="0 0 24 24" fill="none" stroke="#1f6fd0" stroke-width="3"><path d="M4 12.5l5 5L20 6"/></svg>Care Transitions</li>
      <li class="services__item"><svg class="services__tick" viewBox="0 0 24 24" fill="none" stroke="#1f6fd0" stroke-width="3"><path d="M4 12.5l5 5L20 6"/></svg>Case Management</li>
      <li class="services__item"><svg class="services__tick" viewBox="0 0 24 24" fill="none" stroke="#1f6fd0" stroke-width="3"><path d="M4 12.5l5 5L20 6"/></svg>Risk Assessment</li>
      <li class="services__item"><svg class="services__tick" viewBox="0 0 24 24" fill="none" stroke="#1f6fd0" stroke-width="3"><path d="M4 12.5l5 5L20 6"/></svg>Utilization Review</li>
      <li class="services__item"><svg class="services__tick" viewBox="0 0 24 24" fill="none" stroke="#1f6fd0" stroke-width="3"><path d="M4 12.5l5 5L20 6"/></svg>Discharge Planning</li>
    </ul>
  </section>
</body>
</html>
```